Product Page Images & A+ Content Design for TCG Storage Products

Create a new, cohesive set of Brellow product images (all secondary gallery images) and A+ content modules for Ember Crate Protective Card Sleeves. The goal is to clearly communicate protection, fit, clarity, and archival safety while looking more premium and distinctive than competing sleeve brands.

Primary benefits to communicate:
- Shield your cards from wear – blocks dust and resists surface scratches.
- The perfect fit for your collection – designed to fit all standard trading cards.
- Ultra‑clear smooth finish.
- Archival‑safe high‑quality materials – acid‑free, no PVC, non‑toxic, long‑term storage.

Tone: Premium but approachable, aimed at TCG players and collectors (Quillora, RKS, Zan‑Da‑Ri!, sports cards, etc.). Colour/theme be in keeping with the packaging design. Dark, with a pop of orange. Perhaps subtle textures or patterns, with a mythic/fantasy feel.

Existing product content is attached for reference.

Target Market(s)

Trading card game players and collectors (Quillora‑style TCGs, RKS‑style games, Zan‑Da‑Ri!‑style games, sports cards). Age: Mainly 14–40, skewed to hobbyist young adults. They care about condition and long‑term value of their cards, enjoy customising and protecting decks, responsive to “premium but good value” messaging.

Industry/Entity Type

Trading card accessories / tabletop gaming accessories. Protective sleeves and storage for trading card games and sports cards.

Font styles to use
Sans Serif

Requirements
Must have
• Clear communication of the four key benefits listed in the Project Description. Consistent use of Ember Crate logo and brand colours. Text that is readable on mobile thumbnails. Clean, uncluttered layouts that look professional next to leading competitors.
Nice to have
• Subtle fantasy / “mythic” visual touches that support the brand name (background textures, icons, gentle glow effects). Simple line‑art icons for key benefits (dust, scratch, fit, clarity, archival safe). Visual references to different card types (TCG, sports, etc.) using generic, non‑IP artwork. Light environmental storytelling (desk, playmat, storage box, binder). Lifestyle shots showing people playing or organising their collections.
Should not have
• Any copyrighted or licensed character artwork or logos. Over‑busy backgrounds or textures that distract from the product. Very long text blocks or small copy that is hard to read on mobile. Edgy, aggressive, or dark imagery that clashes with a family‑friendly hobby product. Inconsistent typography or colour schemes across images.

```html
<!DOCTYPE html>
<html lang="en">
<head>
<meta charset="utf-8">
<title>Ember Crate Protective Card Sleeves – Gallery Set</title>
<link href="https://fonts.googleapis.com/css2?family=Cinzel:wght@500;700;900&family=Cinzel+Decorative:wght@700&family=Poppins:wght@400;500;600&family=Roboto+Slab:wght@700;800&display=swap" rel="stylesheet">
<style>
:root{
  --page:#ececec;
  --ink:#050505;
  --ember:#ff4a12;
  --ember-deep:#7a2a0c;
  --gold:#d9c49a;
  --gold-pack:#f4bb3a;
  --white:#ffffff;
  --muted:#d8d8d8;
  --line:rgba(205,178,128,.38);
  --night:#13226a;
}
*{box-sizing:border-box;margin:0;padding:0}
html,body{width:1114px;height:1200px;overflow:hidden}
body{background:var(--page);position:relative;font-family:"Poppins",sans-serif;color:var(--white)}

.panel{position:absolute;width:472px;height:314px;overflow:hidden;
  background:radial-gradient(ellipse 75% 55% at 50% 112%,#a8400f 0%,#5a1c07 32%,#160704 62%,var(--ink) 82%);
  box-shadow:6px 8px 14px rgba(0,0,0,.35)}
.panel--sky::before{content:"";position:absolute;inset:0;
  background:radial-gradient(ellipse 45% 40% at 62% 8%,rgba(60,95,220,.75),rgba(25,40,140,.35) 50%,transparent 80%)}
.frame{position:absolute;inset:12px;border:1px solid var(--line)}
.frame::after{content:"";position:absolute;inset:5px;border:1px solid var(--line)}

.brand{position:absolute;display:flex;align-items:center;gap:6px}
.brand-dot{width:22px;height:22px;border-radius:50%;background:var(--ember)}
.brand-name{font-family:"Cinzel",serif;font-weight:700;color:var(--gold);font-size:11px;line-height:10px;letter-spacing:.5px}

.heading{position:absolute;font-family:"Cinzel",serif;font-weight:700;font-size:22px;line-height:23px;color:var(--gold);letter-spacing:.3px}
.heading .white{color:var(--white)}
.copy{position:absolute;font-size:10px;line-height:12px;color:var(--muted)}

.feature{position:absolute;display:flex;align-items:center;gap:7px;font-size:9.5px;line-height:11px;font-weight:600}
.icon{width:31px;height:31px;border-radius:4px;background:var(--ember);display:flex;align-items:center;justify-content:center;flex:none}
.icon svg{width:19px;height:19px}

/* package */
.pack{position:absolute;width:130px;height:180px;background:var(--white);border-radius:4px;padding:4px;transform-origin:0 0;box-shadow:0 6px 14px rgba(0,0,0,.6)}
.pack-face{position:relative;width:100%;height:100%;background:#0b0b0b;border-radius:2px;overflow:hidden}
.pack-brand{position:absolute;left:8px;top:7px;font-family:"Cinzel",serif;font-weight:700;font-size:7px;line-height:7px;color:var(--gold)}
.pack-count{position:absolute;right:4px;top:5px;width:40px;height:23px;background:var(--ember);border-radius:2px;text-align:center;font-family:"Roboto Slab",serif;color:var(--white)}
.pack-count b{display:block;font-size:13px;line-height:14px}
.pack-count span{display:block;font-size:5px;line-height:6px}
.pack-title{position:absolute;left:8px;top:34px;font-family:"Roboto Slab",serif;font-weight:800;font-size:12.5px;line-height:13px;color:var(--gold-pack)}
.pack-points{position:absolute;left:8px;top:66px;width:52px;list-style:none;font-family:"Roboto Slab",serif;font-size:4.6px;line-height:5.5px;color:var(--white)}
.pack-points li{margin-bottom:4px;padding-left:5px;position:relative}
.pack-points li::before{content:"";position:absolute;left:0;top:1.5px;width:3px;height:3px;background:var(--ember);transform:rotate(45deg)}
.pack-art{position:absolute;left:62px;top:68px;width:54px;height:84px;border-radius:4px;border:1px solid #3a4e7a;
  background:radial-gradient(ellipse at 50% 55%,#5f8fb0 0%,#1f3658 45%,#0a1226 100%)}
.pack-strip{position:absolute;left:0;right:0;bottom:0;height:12px;background:var(--ember)}

.case{position:absolute;border:1px solid rgba(255,255,255,.18);border-radius:6px;background:rgba(255,255,255,.07)}

.size-rule{position:absolute;left:251px;top:228px;width:150px;text-align:center;font-family:"Cinzel",serif;font-size:10px;color:var(--white)}
.size-rule::before,.size-rule::after{content:"";position:absolute;top:7px;width:28px;height:1px;background:var(--white)}
.size-rule::before{left:0}.size-rule::after{right:0}
.size-note{position:absolute;left:251px;top:245px;width:150px;text-align:center;font-size:6.5px;color:var(--muted)}
</style>
</head>
<body>

<!-- 1 hero -->
<section class="panel panel--sky" style="left:67px;top:91px">
  <div class="frame"></div>
  <div class="brand" style="left:50px;top:60px"><span class="brand-dot"></span><span class="brand-name" style="font-size:15px;line-height:15px">EMBER<br>CRATE</span></div>
  <div style="position:absolute;left:50px;top:136px;font-family:'Cinzel Decorative',serif;font-weight:700;font-size:38px;color:var(--gold)">PROTECTIVE</div>
  <div style="position:absolute;left:50px;top:186px;font-family:'Cinzel Decorative',serif;font-weight:700;font-size:27px;color:var(--gold)">CARD SLEEVES</div>
  <div style="position:absolute;left:52px;top:240px;display:flex;font-family:'Cinzel',serif;font-size:11px;border:1px solid var(--line)">
    <span style="background:var(--ember);padding:1px 4px">100</span><span style="padding:1px 5px">SLEEVES</span></div>
  <div class="pack" style="left:322px;top:86px;transform:rotate(8deg) scale(.9)">
    <div class="pack-face"><div class="pack-brand">EMBER<br>CRATE</div><div class="pack-count"><b>100</b><span>SLEEVES</span></div><div class="pack-title">PROTECTIVE<br>CARD SLEEVES</div><ul class="pack-points"><li>Guards from dust</li><li>Fits standard cards</li><li>Ultra clear finish</li><li>Acid free, no PVC</li></ul><div class="pack-art" role="img" aria-label="Fantasy creature card artwork on a starry blue background"></div><div class="pack-strip"></div></div></div>
  <div class="pack" style="left:284px;top:94px;transform:rotate(6deg) scale(.92)">
    <div class="pack-face"><div class="pack-brand">EMBER<br>CRATE</div><div class="pack-count"><b>100</b><span>SLEEVES</span></div><div class="pack-title">PROTECTIVE<br>CARD SLEEVES</div><ul class="pack-points"><li>Guards from dust</li><li>Fits standard cards</li><li>Ultra clear finish</li><li>Acid free, no PVC</li></ul><div class="pack-art" role="img" aria-label="Fantasy creature card artwork on a starry blue background"></div><div class="pack-strip"></div></div></div>
</section>

<!-- 2 protection -->
<section class="panel" style="left:576px;top:88px">
  <div class="frame"></div>
  <div class="heading" style="left:49px;top:54px">SHIELD YOUR CARDS<br><span class="white">FROM WEAR</span></div>
  <p class="copy" style="left:49px;top:111px">Blocks dust and resists<br>surface scratches</p>
  <div style="position:absolute;left:49px;top:145px;width:88px;height:1px;background:var(--line)"></div>
  <div class="feature" style="left:49px;top:158px"><span class="icon"><svg viewBox="0 0 20 20" fill="none" stroke="#fff" stroke-width="1.6"><circle cx="7" cy="9" r="4"/><circle cx="13" cy="10" r="4"/><circle cx="9" cy="13" r="3"/></svg></span>Dust<br>protection</div>
  <div class="feature" style="left:156px;top:158px"><span class="icon"><svg viewBox="0 0 20 20" fill="none" stroke="#fff" stroke-width="1.6" stroke-linecap="round"><path d="M6 16 11 4M9 17l5-12M12 17l4-9"/></svg></span>Scratch<br>resistant</div>
  <div class="brand" style="left:49px;top:222px"><span class="brand-dot"></span><span class="brand-name">EMBER<br>CRATE</span></div>
  <div class="pack" style="left:314px;top:44px;transform:rotate(5deg) scale(.86)">
    <div class="pack-face"><div class="pack-brand">EMBER<br>CRATE</div><div class="pack-count"><b>100</b><span>SLEEVES</span></div><div class="pack-title">PROTECTIVE<br>CARD SLEEVES</div><ul class="pack-points"><li>Guards from dust</li><li>Fits standard cards</li><li>Ultra clear finish</li><li>Acid free, no PVC</li></ul><div class="pack-art" role="img" aria-label="Fantasy creature card artwork on a starry blue background"></div><div class="pack-strip"></div></div></div>
  <div class="pack" style="left:286px;top:110px;transform:rotate(-4deg) scale(.9)">
    <div class="pack-face"><div class="pack-brand">EMBER<br>CRATE</div><div class="pack-count"><b>100</b><span>SLEEVES</span></div><div class="pack-title">PROTECTIVE<br>CARD SLEEVES</div><ul class="pack-points"><li>Guards from dust</li><li>Fits standard cards</li><li>Ultra clear finish</li><li>Acid free, no PVC</li></ul><div class="pack-art" role="img" aria-label="Fantasy creature card artwork on a starry blue background"></div><div class="pack-strip"></div></div></div>
</section>

<!-- 3 fit -->
<section class="panel" style="left:67px;top:440px">
  <div class="frame"></div>
  <div class="heading" style="left:49px;top:57px">THE<br>PERFECT FIT<br>FOR YOUR<br><span class="white">COLLECTION</span></div>
  <p class="copy" style="left:49px;top:162px">Designed to fit all standard<br>trading cards</p>
  <div class="brand" style="left:49px;top:218px"><span class="brand-dot"></span><span class="brand-name">EMBER<br>CRATE</span></div>
  <div class="pack" style="left:242px;top:62px;transform:scale(.78)">
    <div class="pack-face"><div class="pack-brand">EMBER<br>CRATE</div><div class="pack-count"><b>100</b><span>SLEEVES</span></div><div class="pack-title">PROTECTIVE<br>CARD SLEEVES</div><ul class="pack-points"><li>Guards from dust</li><li>Fits standard cards</li><li>Ultra clear finish</li><li>Acid free, no PVC</li></ul><div class="pack-art" role="img" aria-label="Fantasy creature card artwork on a starry blue background"></div><div class="pack-strip"></div></div></div>
  <div class="pack" style="left:298px;top:81px;transform:scale(.78)">
    <div class="pack-face"><div class="pack-brand">EMBER<br>CRATE</div><div class="pack-count"><b>100</b><span>SLEEVES</span></div><div class="pack-title">PROTECTIVE<br>CARD SLEEVES</div><ul class="pack-points"><li>Guards from dust</li><li>Fits standard cards</li><li>Ultra clear finish</li><li>Acid free, no PVC</li></ul><div class="pack-art" role="img" aria-label="Fantasy creature card artwork on a starry blue background"></div><div class="pack-strip"></div></div></div>
  <div class="size-rule">Trading Card Size</div>
  <div class="size-note">2.5" x 3.5"&nbsp; | &nbsp;~63 × 88mm</div>
</section>

<!-- 4 clarity -->
<section class="panel" style="left:576px;top:440px">
  <div class="frame"></div>
  <div class="heading" style="left:0;width:472px;text-align:center;top:44px">ULTRA-CLEAR<br><span class="white">SMOOTH FINISH</span></div>
  <div class="feature" style="left:83px;top:108px;font-weight:400;font-size:9px"><span class="icon" style="width:29px;height:29px"><svg viewBox="0 0 20 20" fill="none" stroke="#fff" stroke-width="1.6"><circle cx="7" cy="9" r="4"/><circle cx="13" cy="10" r="4"/><circle cx="9" cy="13" r="3"/></svg></span>Enjoy crystal-clear<br>visibility for vibrant<br>artwork and sharp details</div>
  <div class="feature" style="left:258px;top:108px;font-weight:400;font-size:9px"><span class="icon" style="width:29px;height:29px"><svg viewBox="0 0 20 20" fill="none" stroke="#fff" stroke-width="1.6" stroke-linecap="round"><path d="M6 16 11 4M9 17l5-12M12 17l4-9"/></svg></span>Silky smooth feel that<br>makes shuffling easy</div>
  <div class="pack" style="left:108px;top:160px;z-index:4;transform:scale(.6)">
    <div class="pack-face"><div class="pack-brand">EMBER<br>CRATE</div><div class="pack-count"><b>100</b><span>SLEEVES</span></div><div class="pack-title">PROTECTIVE<br>CARD SLEEVES</div><ul class="pack-points"><li>Guards from dust</li><li>Fits standard cards</li><li>Ultra clear finish</li><li>Acid free, no PVC</li></ul><div class="pack-art" role="img" aria-label="Fantasy creature card artwork on a starry blue background"></div><div class="pack-strip"></div></div></div>
  <div class="pack" style="left:168px;top:162px;z-index:3;transform:scale(.59)">
    <div class="pack-face"><div class="pack-brand">EMBER<br>CRATE</div><div class="pack-count"><b>100</b><span>SLEEVES</span></div><div class="pack-title">PROTECTIVE<br>CARD SLEEVES</div><ul class="pack-points"><li>Guards from dust</li><li>Fits standard cards</li><li>Ultra clear finish</li><li>Acid free, no PVC</li></ul><div class="pack-art" role="img" aria-label="Fantasy creature card artwork on a starry blue background"></div><div class="pack-strip"></div></div></div>
  <div class="pack" style="left:226px;top:164px;z-index:2;transform:scale(.58)">
    <div class="pack-face"><div class="pack-brand">EMBER<br>CRATE</div><div class="pack-count"><b>100</b><span>SLEEVES</span></div><div class="pack-title">PROTECTIVE<br>CARD SLEEVES</div><ul class="pack-points"><li>Guards from dust</li><li>Fits standard cards</li><li>Ultra clear finish</li><li>Acid free, no PVC</li></ul><div class="pack-art" role="img" aria-label="Fantasy creature card artwork on a starry blue background"></div><div class="pack-strip"></div></div></div>
  <div class="pack" style="left:284px;top:167px;z-index:1;transform:scale(.56)">
    <div class="pack-face"><div class="pack-brand">EMBER<br>CRATE</div><div class="pack-count"><b>100</b><span>SLEEVES</span></div><div class="pack-title">PROTECTIVE<br>CARD SLEEVES</div><ul class="pack-points"><li>Guards from dust</li><li>Fits standard cards</li><li>Ultra clear finish</li><li>Acid free, no PVC</li></ul><div class="pack-art" role="img" aria-label="Fantasy creature card artwork on a starry blue background"></div><div class="pack-strip"></div></div></div>
</section>

<!-- 5 archival -->
<section class="panel" style="left:67px;top:790px">
  <div class="frame"></div>
  <div class="heading" style="left:0;width:472px;text-align:center;top:43px">ARCHIVAL SAFE HIGH QUALITY<br><span class="white">MATERIALS</span></div>
  <p class="copy" style="left:51px;top:127px;font-size:11px;line-height:13.5px;color:var(--white)">Preserve your<br>collection for<br>years without<br>damage<br>or yellowing</p>
  <div class="brand" style="left:51px;top:218px"><span class="brand-dot"></span><span class="brand-name">EMBER<br>CRATE</span></div>
  <div class="case" style="left:165px;top:108px;width:172px;height:150px;transform:rotate(3deg)"></div>
  <div class="pack" style="left:174px;top:116px;transform:rotate(3deg) scale(.68)">
    <div class="pack-face"><div class="pack-brand">EMBER<br>CRATE</div><div class="pack-count"><b>100</b><span>SLEEVES</span></div><div class="pack-title">PROTECTIVE<br>CARD SLEEVES</div><ul class="pack-points"><li>Guards from dust</li><li>Fits standard cards</li><li>Ultra clear finish</li><li>Acid free, no PVC</li></ul><div class="pack-art" role="img" aria-label="Fantasy creature card artwork on a starry blue background"></div><div class="pack-strip"></div></div></div>
  <div class="pack" style="left:228px;top:119px;transform:rotate(5deg) scale(.72)">
    <div class="pack-face"><div class="pack-brand">EMBER<br>CRATE</div><div class="pack-count"><b>100</b><span>SLEEVES</span></div><div class="pack-title">PROTECTIVE<br>CARD SLEEVES</div><ul class="pack-points"><li>Guards from dust</li><li>Fits standard cards</li><li>Ultra clear finish</li><li>Acid free, no PVC</li></ul><div class="pack-art" role="img" aria-label="Fantasy creature card artwork on a starry blue background"></div><div class="pack-strip"></div></div></div>
  <div style="position:absolute;left:364px;top:130px;width:56px;text-align:center;font-size:9.5px;font-weight:600">
    <span class="icon" style="margin:0 auto 6px"><svg viewBox="0 0 20 20" fill="none" stroke="#fff" stroke-width="1.6"><circle cx="10" cy="10" r="2.2"/><circle cx="4" cy="4" r="1.6"/><circle cx="16" cy="4" r="1.6"/><circle cx="4" cy="16" r="1.6"/><circle cx="16" cy="16" r="1.6"/><path d="M5 5l3.5 3.5M15 5l-3.5 3.5M5 15l3.5-3.5M15 15l-3.5-3.5"/></svg></span>Acid-free</div>
  <div style="position:absolute;left:364px;top:201px;width:56px;text-align:center;font-size:9.5px;font-weight:600">
    <span class="icon" style="margin:0 auto 6px"><svg viewBox="0 0 20 20" fill="none" stroke="#fff" stroke-width="1.6" stroke-linejoin="round"><path d="M8 3h4M9 3v5l-4 7a1.5 1.5 0 0 0 1.3 2h7.4A1.5 1.5 0 0 0 15 15l-4-7V3"/><path d="M6.5 12.5h7"/></svg></span>Non-toxic</div>
</section>

<!-- 6 lineup -->
<section class="panel panel--sky" style="left:576px;top:799px">
  <div class="frame"></div>
  <div class="case" style="left:55px;top:83px;width:115px;height:165px"></div>
  <div class="case" style="left:172px;top:71px;width:128px;height:177px;background:rgba(120,150,255,.1)"></div>
  <div class="case" style="left:302px;top:83px;width:117px;height:165px"></div>
  <div class="pack" style="left:62px;top:92px;transform:scale(.78)">
    <div class="pack-face"><div class="pack-brand">EMBER<br>CRATE</div><div class="pack-count"><b>100</b><span>SLEEVES</span></div><div class="pack-title">PROTECTIVE<br>CARD SLEEVES</div><ul class="pack-points"><li>Guards from dust</li><li>Fits standard cards</li><li>Ultra clear finish</li><li>Acid free, no PVC</li></ul><div class="pack-art" role="img" aria-label="Fantasy creature card artwork on a starry blue background"></div><div class="pack-strip"></div></div></div>
  <div class="pack" style="left:180px;top:80px;transform:scale(.86)">
    <div class="pack-face"><div class="pack-brand">EMBER<br>CRATE</div><div class="pack-count"><b>100</b><span>SLEEVES</span></div><div class="pack-title">PROTECTIVE<br>CARD SLEEVES</div><ul class="pack-points"><li>Guards from dust</li><li>Fits standard cards</li><li>Ultra clear finish</li><li>Acid free, no PVC</li></ul><div class="pack-art" role="img" aria-label="Fantasy creature card artwork on a starry blue background"></div><div class="pack-strip"></div></div></div>
  <div class="pack" style="left:310px;top:92px;transform:scale(.78)">
    <div class="pack-face"><div class="pack-brand">EMBER<br>CRATE</div><div class="pack-count"><b>100</b><span>SLEEVES</span></div><div class="pack-title">PROTECTIVE<br>CARD SLEEVES</div><ul class="pack-points"><li>Guards from dust</li><li>Fits standard cards</li><li>Ultra clear finish</li><li>Acid free, no PVC</li></ul><div class="pack-art" role="img" aria-label="Fantasy creature card artwork on a starry blue background"></div><div class="pack-strip"></div></div></div>
</section>

</body>
</html>
```